Dalvick's Business Card

I need some designs for a new business card including the new logo attached. An old example of our business card is also attached to show all the data that should be included on the new design.
**I added some more examples someone had mocked up**

Contact Information for Business Card

Should include all info on other examples uploaded.

```html
<!DOCTYPE html>
<html lang="en">
<head>
<meta charset="UTF-8">
<title>Dalvick's Business Card</title>
<link href="https://fonts.googleapis.com/css2?family=Montserrat:wght@500;600;700;800&display=swap" rel="stylesheet">
<style>
  :root {
    --brand-blue: #0b72b9;
    --brand-red: #e8202a;
    --paper: #ffffff;
    --backdrop: #e6e5e6;
  }
  * { margin: 0; padding: 0; box-sizing: border-box; }
  html, body { width: 1200px; height: 1200px; overflow: hidden; }
  body {
    background: var(--backdrop);
    font-family: "Montserrat", sans-serif;
    position: relative;
  }
  .card {
    position: absolute;
    left: 140px;
    width: 920px;
    height: 526px;
    background: var(--paper);
    overflow: hidden;
    box-shadow: 0 18px 40px rgba(0,0,0,0.22);
  }
  .card--front { top: 50px; }
  .card--back { top: 624px; }

  .band { position: absolute; left: 0; width: 100%; color: var(--paper); font-weight: 500; text-transform: uppercase; display: flex; align-items: center; white-space: nowrap; }
  .band--top { top: 0; height: 96px; background: var(--brand-blue); font-size: 29px; letter-spacing: 1px; padding-left: 52px; }
  .band--bottom { bottom: 0; height: 84px; background: var(--brand-red); font-size: 18px; letter-spacing: 0.5px; padding-left: 52px; }
  .notch { position: absolute; width: 0; height: 0; }
  .notch--down { top: 96px; left: 300px; border-left: 34px solid transparent; border-right: 34px solid transparent; border-top: 28px solid var(--brand-blue); }
  .notch--up { bottom: 84px; left: 560px; border-left: 34px solid transparent; border-right: 34px solid transparent; border-bottom: 28px solid var(--brand-red); }

  .brand { position: absolute; display: flex; align-items: center; gap: 18px; white-space: nowrap; }
  .brand__mark { border-radius: 50%; flex: none; }
  .brand__name { font-weight: 800; line-height: 1; letter-spacing: 2px; text-transform: uppercase; }
  .brand__tagline { font-weight: 600; text-transform: uppercase; letter-spacing: 1px; margin-top: 6px; }

  .card--front .brand { left: 170px; top: 200px; }
  .card--front .brand__mark { width: 110px; height: 110px; background: var(--brand-blue); }
  .card--front .brand__name { font-size: 96px; color: var(--brand-blue); }
  .card--front .brand__tagline { font-size: 20px; color: var(--brand-red); }

  .wave { position: absolute; inset: 0; }
  .holder-name { position: absolute; left: 60px; top: 120px; font-size: 40px; font-weight: 800; color: var(--brand-blue); letter-spacing: 1px; text-transform: uppercase; white-space: nowrap; }

  .card--back .brand { left: 530px; top: 230px; gap: 12px; }
  .card--back .brand__mark { width: 56px; height: 56px; background: var(--paper); }
  .card--back .brand__name { font-size: 44px; color: var(--paper); letter-spacing: 1px; }
  .card--back .brand__tagline { font-size: 10.5px; color: var(--paper); }

  .contact { position: absolute; left: 70px; top: 345px; color: var(--paper); font-size: 24px; font-weight: 500; white-space: nowrap; }
  .contact__line { display: flex; align-items: center; gap: 12px; margin-bottom: 4px; }
  .contact__line svg { width: 20px; height: 20px; flex: none; }
  .credentials { margin-top: 18px; text-transform: uppercase; font-size: 24px; line-height: 1.3; letter-spacing: 1px; }
</style>
</head>
<body>
  <section class="card card--front">
    <div class="band band--top">Serves Alder Creek, IA &amp; Surrounding Areas</div>
    <div class="notch notch--down"></div>
    <div class="brand">
      <span class="brand__mark"></span>
      <div>
        <div class="brand__name">Dalvick's</div>
        <div class="brand__tagline">Air Conditioning &amp; Heating Service</div>
      </div>
    </div>
    <div class="notch notch--up"></div>
    <div class="band band--bottom">Call today for all your HVAC, Refrigeration &amp; Plumbing Needs</div>
  </section>

  <section class="card card--back">
    <svg class="wave" viewBox="0 0 920 526" preserveAspectRatio="none" aria-hidden="true">
      <path d="M0,288 C220,318 420,290 560,158 C660,58 730,8 920,8 L920,526 L0,526 Z" fill="var(--brand-red)"/>
      <path d="M0,302 C220,332 420,304 560,172 C660,72 730,22 920,22 L920,526 L0,526 Z" fill="var(--brand-blue)"/>
    </svg>
    <div class="holder-name">Glen Dalvick</div>
    <div class="brand">
      <span class="brand__mark"></span>
      <div>
        <div class="brand__name">Dalvick's</div>
        <div class="brand__tagline">Air Conditioning &amp; Heating Service</div>
      </div>
    </div>
    <div class="contact">
      <div class="contact__line">
        <svg viewBox="0 0 24 24"><path fill="#fff" d="M6.6 10.8a15 15 0 0 0 6.6 6.6l2.2-2.2a1 1 0 0 1 1-.25 11.4 11.4 0 0 0 3.6.57 1 1 0 0 1 1 1V20a1 1 0 0 1-1 1A17 17 0 0 1 3 4a1 1 0 0 1 1-1h3.5a1 1 0 0 1 1 1c0 1.25.2 2.45.57 3.57a1 1 0 0 1-.25 1z"/></svg>
        <span>555.014.2290</span>
      </div>
      <div class="contact__line">
        <svg viewBox="0 0 24 24"><path fill="#fff" d="M2 5h20v14H2z"/><path fill="none" stroke="#0b72b9" stroke-width="2" d="M2 5l10 8 10-8"/></svg>
        <span>hvacdalvick@mailbox.com</span>
      </div>
      <div class="credentials">
        Licensed &amp; Insured<br>
        Family Owned &amp; Operated
      </div>
    </div>
  </section>
</body>
</html>
```